Beacon Advisory Website

I currently have a website www.beaconadvisoryinc.com. We are a IT Consulting Company. Our website will pretty much tell out our services. I am looking to enhance my website and make it look more professional. Looking for very classy and Contemporary look and design for my website.

It Company

```html
<!DOCTYPE html>
<html lang="en">
<head>
<meta charset="utf-8">
<title>Beacon Advisory — IT Consulting</title>
<link href="https://fonts.googleapis.com/css2?family=Montserrat:ital,wght@0,400;0,500;0,600;0,700;1,400&family=Open+Sans:ital,wght@0,400;0,600;1,400&display=swap" rel="stylesheet">
<style>
  :root {
    --brand-blue: #1a5fa2;
    --accent-orange: #f15a2b;
    --ink: #1f1f1f;
    --rule-light: rgba(255,255,255,0.35);
    --white: #ffffff;
    --page: #ffffff;
  }
  * { box-sizing: border-box; margin: 0; padding: 0; }
  html, body { width: 1200px; height: 2857px; overflow: hidden; }
  body { position: relative; background: var(--page); font-family: "Open Sans", Arial, sans-serif; color: var(--ink); }
  h1, h2, h3 { font-weight: 400; }

  /* Header */
  .site-header { position: absolute; left: 0; top: 0; width: 1200px; height: 72px; background: var(--white); }
  .brand { position: absolute; left: 118px; top: 20px; display: flex; align-items: center; gap: 10px; }
  .brand-mark { width: 28px; height: 28px; background: var(--brand-blue); }
  .brand-name { font-family: "Montserrat", sans-serif; font-weight: 700; font-size: 20px; color: var(--brand-blue); }
  .main-nav { position: absolute; top: 30px; left: 0; font-family: "Montserrat", sans-serif; font-size: 12px; color: #555; text-transform: uppercase; }
  .main-nav span { position: absolute; white-space: nowrap; }
  .main-nav .is-active { color: var(--brand-blue); }
  .join-btn { position: absolute; left: 971px; top: 23px; width: 109px; height: 28px; background: var(--brand-blue); color: var(--white); font-family: "Montserrat", sans-serif; font-size: 12px; display: flex; align-items: center; justify-content: center; text-transform: uppercase; }
  .dropdown { position: absolute; left: 451px; top: 59px; width: 119px; height: 111px; background: var(--brand-blue); z-index: 5; font-size: 13px; color: var(--white); }
  .dropdown div { height: 37px; line-height: 37px; padding-left: 18px; }
  .dropdown .is-hover { background: #2a72b8; }

  /* Hero */
  .hero { position: absolute; left: 0; top: 72px; width: 1200px; height: 541px; background: linear-gradient(120deg, #3a4450 0%, #5b6570 35%, #2c3640 70%, #1f262e 100%); }
  .hero-shade { position: absolute; inset: 0; background: linear-gradient(90deg, rgba(20,26,34,0.55), rgba(20,26,34,0.15)); }
  .hero-title { position: absolute; left: 118px; top: 175px; font-family: "Montserrat", sans-serif; font-weight: 700; font-size: 46px; color: var(--white); letter-spacing: 0.5px; }
  .hero-copy { position: absolute; left: 118px; top: 236px; width: 390px; font-size: 14px; line-height: 19px; color: var(--white); }
  .cta { position: absolute; left: 120px; top: 317px; width: 219px; height: 47px; }
  .cta-label { position: absolute; left: 28px; top: 0; line-height: 47px; font-family: "Montserrat", sans-serif; font-weight: 600; font-size: 16px; color: var(--white); }

  /* Email band */
  .signup { position: absolute; left: 0; top: 613px; width: 1200px; height: 170px; background: var(--brand-blue); }
  .signup-text { position: absolute; left: 138px; top: 54px; width: 440px; text-align: center; font-family: "Montserrat", sans-serif; font-size: 25px; line-height: 32px; color: var(--white); }
  .signup-input { position: absolute; left: 617px; top: 69px; width: 326px; height: 48px; background: var(--white); font-size: 14px; color: #888; padding-left: 22px; line-height: 48px; }
  .signup-go { position: absolute; left: 947px; top: 69px; width: 59px; height: 48px; background: var(--accent-orange); color: var(--white); font-family: "Montserrat", sans-serif; font-weight: 600; font-size: 19px; text-align: center; line-height: 48px; }

  /* About */
  .about-title { position: absolute; left: 118px; top: 963px; font-family: "Montserrat", sans-serif; font-weight: 400; font-size: 29px; color: var(--ink); z-index: 2; }
  .about-copy { position: absolute; left: 118px; top: 1020px; width: 478px; font-size: 13px; line-height: 18.5px; color: var(--ink); z-index: 2; }
  .btn-small { position: absolute; height: 26px; background: var(--accent-orange); color: var(--white); font-family: "Montserrat", sans-serif; font-size: 11px; text-transform: uppercase; text-align: center; line-height: 26px; }
  .laptop-lid { position: absolute; left: 682px; top: 895px; width: 518px; height: 370px; border-radius: 14px 0 0 0; background: linear-gradient(160deg, #eceef0 0%, #dfe2e5 100%); border: 2px solid #cfd3d7; border-right: none; border-bottom: none; }
  .laptop-screen { position: absolute; left: 28px; top: 30px; width: 490px; height: 308px; background: linear-gradient(135deg, #d9d2cc 0%, #bfb7b0 50%, #9aa6b2 100%); }
  .laptop-base { position: absolute; left: 577px; top: 1265px; width: 623px; height: 24px; border-radius: 12px 0 0 30px; background: linear-gradient(180deg, #e6e8ea 0%, #c4c8cc 100%); }

  /* Services */
  .services { position: absolute; left: 0; top: 1393px; width: 1200px; height: 697px; background: var(--brand-blue); color: var(--white); }
  .svc-rule-h { position: absolute; left: 423px; width: 354px; height: 1px; background: var(--rule-light); }
  .svc-rule-v { position: absolute; left: 600px; top: 121px; width: 1px; height: 393px; background: var(--rule-light); }
  .svc-icon { position: absolute; width: 140px; height: 140px; }
  .svc-item { position: absolute; width: 290px; }
  .svc-item h3 { font-family: "Montserrat", sans-serif; font-weight: 400; font-size: 16px; margin-bottom: 8px; }
  .svc-item p { font-size: 13px; line-height: 18.5px; }
  .svc-left { text-align: right; }

  /* Team */
  .team-title { position: absolute; left: 0; top: 2166px; width: 1200px; text-align: center; font-family: "Montserrat", sans-serif; font-weight: 400; font-size: 25px; color: var(--ink); }
  .team-photo { position: absolute; left: 217px; top: 2257px; width: 404px; height: 404px; background: linear-gradient(180deg, #e9e9e9 0%, #d8d8d8 60%, #3a3a3a 100%); }
  .member-name { position: absolute; left: 659px; top: 2255px; font-family: "Montserrat", sans-serif; font-style: italic; font-size: 26px; color: var(--brand-blue); }
  .member-role { position: absolute; left: 659px; top: 2304px; font-size: 12px; font-style: italic; color: #777; line-height: 22px; }
  .member-bio { position: absolute; left: 659px; top: 2364px; width: 400px; font-size: 14px; line-height: 19px; color: var(--ink); }
  .member-social { position: absolute; left: 659px; top: 2474px; display: flex; align-items: center; }
  .member-social span { width: 10px; height: 10px; border-radius: 50%; background: #888; margin: 0 14px; }
  .member-social span:first-child { margin-left: 2px; }
  .member-social i { width: 1px; height: 40px; background: #ccc; }
  .thumbs { position: absolute; left: 657px; top: 2541px; display: flex; gap: 5px; }
  .thumb { width: 63px; height: 63px; background: #2b2b2b; }
  .thumb.is-current { background: #d9d9d9; }

  /* Footer */
  .site-footer { position: absolute; left: 0; top: 2745px; width: 1200px; height: 112px; background: var(--brand-blue); color: var(--white); }
  .footer-nav { position: absolute; top: 59px; left: 0; font-family: "Montserrat", sans-serif; font-size: 11px; text-transform: uppercase; }
  .footer-nav span { position: absolute; white-space: nowrap; }
  .footer-social { position: absolute; left: 972px; top: 58px; display: flex; gap: 14px; }
  .footer-social span { width: 16px; height: 16px; border-radius: 50%; background: var(--white); }
  .copyright { position: absolute; right: 120px; top: 91px; font-size: 10px; }
</style>
</head>
<body>

<header class="site-header">
  <div class="brand"><div class="brand-mark"></div><div class="brand-name">Beacon Advisory</div></div>
  <nav class="main-nav">
    <span class="is-active" style="left:453px">Company</span>
    <span style="left:535px">Services</span>
    <span style="left:613px">Solution</span>
    <span style="left:695px">SResources</span>
    <span style="left:794px">Career</span>
    <span style="left:861px">Contact Us</span>
  </nav>
  <div class="join-btn">Join Us Free</div>
</header>

<div class="dropdown">
  <div>What we do</div>
  <div class="is-hover">Our Process</div>
  <div>Who we are</div>
</div>

<section class="hero">
  <div class="hero-shade" role="img" aria-label="Photo of two consultants in suits working together at a laptop in an office"></div>
  <h1 class="hero-title">CONSULTING</h1>
  <p class="hero-copy">Beacon Advisory has certified professional consultants to work with you to help increase the business by providing IT services</p>
  <div class="cta">
    <svg width="219" height="47" viewBox="0 0 219 47"><polygon points="0,0 200,0 219,23.5 200,47 0,47" fill="#f15a2b"/><circle cx="179" cy="23.5" r="9" fill="none" stroke="#fff" stroke-width="1.8"/><polyline points="174.5,23.5 178,27 183.5,20" fill="none" stroke="#fff" stroke-width="1.8"/></svg>
    <span class="cta-label">Get Started Now</span>
  </div>
</section>

<section class="signup">
  <p class="signup-text">Submit your e-mail receive back<br>details within 24 hours</p>
  <div class="signup-input">Enter your email id</div>
  <div class="signup-go">GO</div>
</section>

<section class="about">
  <div class="laptop-lid">
    <div class="laptop-screen" role="img" aria-label="Photo of a woman working at a desktop computer in a bright office"></div>
  </div>
  <div class="laptop-base"></div>
  <h2 class="about-title">About Us</h2>
  <p class="about-copy">Today's IT market is a dynamic, fast-paced industry, with ever-increasing demands. Meeting these demands for over 25 years, Beacon Advisory maintains a global presence, aggressively recruiting expertly qualified IT and Management Professionals from around the world and cultivating key partnerships with corporations to understand their business models end-to-end, with a goal of delivering exceptional client service and ensuring a consistent delivery of the talent needed to drive results.</p>
  <div class="btn-small" style="left:122px;top:1194px;width:107px">Learn More</div>
</section>

<section class="services">
  <div class="svc-rule-h" style="top:121px"></div>
  <div class="svc-rule-h" style="top:514px"></div>
  <div class="svc-rule-v"></div>

  <svg class="svc-icon" style="left:431px;top:154px" viewBox="0 0 140 140">
    <circle cx="70" cy="70" r="68" fill="none" stroke="#fff" stroke-width="2.5"/>
    <g fill="#fff" transform="translate(70 70)">
      <rect x="-5" y="-25" width="10" height="10"/><rect x="-5" y="15" width="10" height="10"/>
      <rect x="-25" y="-5" width="10" height="10"/><rect x="15" y="-5" width="10" height="10"/>
      <g transform="rotate(45)"><rect x="-5" y="-25" width="10" height="10"/><rect x="-5" y="15" width="10" height="10"/><rect x="-25" y="-5" width="10" height="10"/><rect x="15" y="-5" width="10" height="10"/></g>
      <circle r="18"/>
    </g>
    <circle cx="70" cy="70" r="7" fill="#1a5fa2"/>
  </svg>
  <svg class="svc-icon" style="left:629px;top:154px" viewBox="0 0 140 140">
    <circle cx="70" cy="70" r="68" fill="none" stroke="#fff" stroke-width="2.5"/>
    <g fill="#fff">
      <polygon points="22,62 34,46 50,58 38,74"/>
      <polygon points="118,62 106,46 90,58 102,74"/>
      <path d="M48 56 L68 50 L84 54 L96 66 L80 88 L64 92 L46 78 Z"/>
    </g>
    <path d="M62 66 L72 76 M66 80 L74 88 M56 72 L64 80" stroke="#1a5fa2" stroke-width="3"/>
  </svg>
  <svg class="svc-icon" style="left:431px;top:345px" viewBox="0 0 140 140">
    <circle cx="70" cy="70" r="68" fill="none" stroke="#fff" stroke-width="2.5"/>
    <rect x="56" y="40" width="28" height="60" rx="4" fill="none" stroke="#fff" stroke-width="3.5"/>
    <circle cx="70" cy="93" r="2.5" fill="#fff"/>
  </svg>
  <svg class="svc-icon" style="left:629px;top:345px" viewBox="0 0 140 140">
    <circle cx="70" cy="70" r="68" fill="none" stroke="#fff" stroke-width="2.5"/>
    <path fill="#fff" d="M44 96 V66 L58 58 V66 L72 58 V66 L86 58 V48 H94 V96 Z"/>
    <rect x="54" y="76" width="8" height="8" fill="#1a5fa2"/><rect x="68" y="76" width="8" height="8" fill="#1a5fa2"/><rect x="82" y="76" width="8" height="8" fill="#1a5fa2"/>
  </svg>

  <div class="svc-item svc-left" style="left:91px;top:181px"><h3>Technology</h3><p>Lorem ipsum dolor sit amet, consectetur adipisicing elit, sed do eiusmod tempor incididunt ut labore</p></div>
  <div class="svc-item" style="left:817px;top:181px"><h3>Offshore Business</h3><p>Lorem ipsum dolor sit amet, consectetur adipisicing elit, sed do eiusmod tempor incididunt ut labore</p></div>
  <div class="svc-item svc-left" style="left:99px;top:370px"><h3>Application Developement</h3><p>Lorem ipsum dolor sit amet, consectetur adipisicing elit, sed do eiusmod tempor incididunt ut labore</p></div>
  <div class="svc-item" style="left:810px;top:370px"><h3>Enterprise Integration</h3><p>Lorem ipsum dolor sit amet, consectetur adipisicing elit, sed do eiusmod tempor incididunt ut labore</p></div>

  <div class="btn-small" style="left:543px;top:571px;width:114px;height:34px;line-height:34px">Learn More</div>
</section>

<section class="team">
  <h2 class="team-title">Our Team</h2>
  <div class="team-photo" role="img" aria-label="Portrait photo of a smiling team member in glasses and a dark suit"></div>
  <div class="member-name">Daniel Reyes</div>
  <div class="member-role">Executive Director<br>beaconadvisoryinc.com</div>
  <p class="member-bio">Lorem ipsum dolor sit amet, consectetur adipisicing elit, sed do eiusmod incididunt ut labore et dolore magna aliqua. Lorem ipsum dolor sit amet, consectetur adipisicing elit, sed do eiusmod incididunt ut labore et dolore magna aliqua.</p>
  <div class="member-social"><span></span><i></i><span></span><i></i><span></span></div>
  <div class="thumbs" role="img" aria-label="Row of team member portrait thumbnails">
    <div class="thumb"></div><div class="thumb is-current"></div><div class="thumb"></div><div class="thumb"></div>
  </div>
</section>

<footer class="site-footer">
  <nav class="footer-nav">
    <span style="left:118px">Company</span>
    <span style="left:200px">Services</span>
    <span style="left:278px">Solution</span>
    <span style="left:360px">SResources</span>
    <span style="left:459px">Career</span>
    <span style="left:527px">Contact Us</span>
  </nav>
  <div class="footer-social"><span></span><span></span><span></span><span></span></div>
  <div class="copyright">© 2015</div>
</footer>

</body>
</html>
```